Law Firm Business Card

This is a business card for a law firm that serves US military and veterans.

The card must have ONLY the following (we want an uncluttered look):

- Company logo (PNG, GIF, JPEG copies uploaded)
- A tagline reading: "a law firm for service members and veterans"
- My name and title: "Tobias Marlow" and "Attorney"
- My email: "tobias.marlow@brinmoorlegal.com"
- My number: "855-FIRM-ONE (347-6663)"

We are looking for a clean, simple layout with only the above information, likely printed on a bright white cotton stock. The font of our logo is DIN 1451, and the font used on our website is Helvetica Neue. The color of our logo is #336699, and we probably want the tagline in that color also, and my contact information in a dark grey. Please review our website at www.brinmoorlegal.com to ensure your card design complements our website style.

Thanks and we look forward to seeing your submissions.

A few notes:

- Two-sided submissions are ok
- Please don't add graphics (scales of justice, judges hammer, etc)

```html
<!DOCTYPE html>
<html lang="en">
<head>
<meta charset="utf-8">
<title>Brinmoor Legal – Business Card</title>
<link href="https://fonts.googleapis.com/css2?family=Crimson+Pro:ital,wght@0,400;0,600;1,600&display=swap" rel="stylesheet">
<style>
  :root {
    --brand-blue: #2a6bcc;
    --card-white: #ffffff;
    --ink-dark: #1d1d1d;
    --rule-blue: #2a5aa8;
    --stage: #e9e6e2;
  }
  * { box-sizing: border-box; margin: 0; padding: 0; }
  html, body {
    width: 1200px; height: 501px; overflow: hidden;
    background: var(--stage);
    font-family: "Crimson Pro", "Palatino Linotype", Georgia, serif;
  }
  .stage {
    position: relative; width: 1200px; height: 501px;
    display: flex; align-items: center; justify-content: center; gap: 60px;
  }
  .card {
    width: 480px; height: 280px; border-radius: 26px;
    display: flex; flex-direction: column; align-items: center;
    box-shadow: 0 10px 24px rgba(0,0,0,0.18);
  }
  .card--front { background: var(--card-white); padding-top: 40px; }
  .card--back { background: var(--brand-blue); justify-content: center; }

  .brand {
    display: flex; align-items: center; gap: 12px;
    font-weight: 600; text-transform: uppercase; letter-spacing: 2px;
    line-height: 1;
  }
  .brand__mark { width: 14px; height: 14px; }
  .card--front .brand { color: var(--brand-blue); font-size: 46px; }
  .card--front .brand__mark { background: var(--brand-blue); }
  .card--back .brand { color: var(--card-white); font-size: 54px; }
  .card--back .brand__mark { background: var(--card-white); width: 16px; height: 16px; }

  .tagline { font-size: 17px; margin-top: 14px; }
  .card--front .tagline { color: var(--brand-blue); }
  .card--back .tagline { color: var(--card-white); font-size: 21px; margin-top: 22px; }

  .person {
    margin-top: 18px; width: 200px; text-align: center;
    padding-bottom: 6px; border-bottom: 1.5px solid var(--rule-blue);
    font-size: 17px; color: var(--ink-dark);
  }
  .person__name { color: var(--brand-blue); font-style: italic; font-weight: 600; font-size: 20px; }

  .contact { margin-top: 12px; list-style: none; font-size: 16px; color: var(--ink-dark); }
  .contact li { display: flex; align-items: center; gap: 8px; line-height: 1.35; }
  .contact svg { width: 13px; height: 13px; flex: none; }
</style>
</head>
<body>
<main class="stage">
  <section class="card card--front" aria-label="Card front">
    <div class="brand"><span class="brand__mark"></span>Brinmoor Legal</div>
    <p class="tagline">A Law Firm For Service Members And Veterans</p>
    <p class="person"><span class="person__name">Tobias Marlow</span>, Attorney</p>
    <ul class="contact">
      <li>
        <svg viewBox="0 0 16 16" aria-hidden="true"><circle cx="8" cy="8" r="7" fill="none" stroke="#1d1d1d" stroke-width="1.3"/><path d="M5.5 4.5l1.5 0 .6 2-1 .8a5 5 0 0 0 2 2l.8-1 2 .6v1.5c-3.5.4-6.3-2.4-5.9-5.9z" fill="#1d1d1d"/></svg>
        855-FIRM-ONE (347-6663)
      </li>
      <li>
        <svg viewBox="0 0 16 16" aria-hidden="true"><rect x="1.5" y="4" width="13" height="9" fill="none" stroke="#1d1d1d" stroke-width="1.3"/><path d="M1.5 4l6.5 5 6.5-5" fill="none" stroke="#1d1d1d" stroke-width="1.3"/></svg>
        tobias.marlow@brinmoorlegal.com
      </li>
    </ul>
  </section>

  <section class="card card--back" aria-label="Card back">
    <div class="brand"><span class="brand__mark"></span>Brinmoor Legal</div>
    <p class="tagline">A Law Firm For Service Members &amp; Veterans</p>
  </section>
</main>
</body>
</html>
```